UI Improvement for FlorKeep app

We are looking for a talented UI/UX designer to REFINE and enhance the visual design of our mobile application, FlorKeep. The app is fully functional, but we need a designer to improve its aesthetics by specifying design elements such as fonts, colors, spacing, and component styles.
Your task will be to analyze the CURRENT UI and provide detailed design specifications that will make the app more visually appealing, modern, and user-friendly.
TODO:
Review the existing FlorKeep app design (see attachments) and identify areas for visual improvement.
Provide a detailed UI style guide, including:
Typography (font choices, sizes, and weights)
Color palette (primary, secondary, and accent colors)
Component styling (buttons, forms, icons, and interactive elements)
Spacing and layout guidelines (margins, paddings, and alignment)
Ensure the design remains clean, modern, and professional while maintaining usability and accessibility.
Provide design mockups or visual examples (if possible) to illustrate the proposed changes.
Deliverables:
A UI Style Guide (PDF or Figma file) with specifications on fonts, colors, spacing, and UI components.
Optionally, before/after mockups or examples demonstrating the improvements.
Ideal Designer:
Strong experience in mobile UI/UX design.
Understanding of modern design trends and best practices.
Ability to communicate design choices clearly for easy developer implementation.
I have attached 7 images showcasing the main UI screens used in the FlorKeep app. These screens need visual enhancements to improve their overall look and user experience.
The images represent the current design in three key modes:
LIST Mode – Displays data in a structured list format.
READ Mode – Shows detailed information when a user selects an item.
ADD/EDIT Mode – Allows users to input or modify information.
Additionally, there is a ‘MORE’ page, which serves as a menu listing other features of the application.
Task Objective:
Please refine and improve these UIs to create a more modern, visually appealing, and user-friendly experience. Focus on typography, colors, spacing, and component styling to ensure a cohesive and polished design.
Look and feel
Each slider illustrates characteristics of the customer's brand and the style your logo design should communicate.

```html
<!DOCTYPE html>
<html lang="en">
<head>
<meta charset="utf-8">
<title>FlorKeep – Contact, Pilots, More</title>
<link href="https://fonts.googleapis.com/css2?family=Montserrat:wght@500;600;700&display=swap" rel="stylesheet">
<style>
  :root{
    --bg:#e3e9f4;
    --panel:#ffffff;
    --navy:#1b4a97;
    --head-a:#1c4d9b;
    --head-b:#26a6d8;
    --card:#e6ecf6;
    --text:#22262e;
    --line:#c7cdd6;
  }
  *{box-sizing:border-box;margin:0;padding:0}
  html,body{width:1200px;height:931px;overflow:hidden;background:var(--bg);font-family:'Montserrat',sans-serif;color:var(--text)}
  .screen{position:absolute;top:30px;width:372px;height:872px;background:var(--panel);overflow:hidden}
  .screen--contact{left:28px}.screen--pilots{left:414px}.screen--more{left:801px}
  .appbar{height:82px;background:linear-gradient(90deg,var(--head-a),var(--head-b));color:#fff;display:flex;align-items:center;padding:0 22px 0 21px;position:relative}
  .appbar__title{font-weight:700;font-size:16.5px;display:flex;align-items:center;gap:7px;margin-top:10px}
  .appbar__actions{margin-left:auto;display:flex;align-items:center;gap:16px;margin-top:0}
  .btn-save{border:1.3px solid #fff;border-radius:10px;color:#fff;font-weight:700;font-size:16px;padding:4px 17px;margin-top:9px}
  .field{position:absolute;border:1px solid var(--line);border-radius:6px;height:58px;padding:18px 17px;font-size:14.5px;font-weight:500}
  .card{position:absolute;left:23px;width:327px;height:80px;background:var(--card);border-radius:14px;padding:13px 0 0 53px;font-size:15.5px;font-weight:500;line-height:27px}
  .card .ico{position:absolute;left:4px;top:4px}
  .card .date{display:flex;align-items:center;gap:4px}
  .menu-item{position:absolute;left:23px;width:326px;height:47px;border:1px solid var(--line);border-radius:24px;display:flex;align-items:center;gap:11px;padding-left:2px;font-size:17px;font-weight:500;letter-spacing:.3px}
  .badge{width:41px;height:41px;border-radius:50%;background:var(--navy);display:flex;align-items:center;justify-content:center;flex:none}
  .tabbar{position:absolute;left:0;right:0;top:757px;bottom:0;box-shadow:0 -6px 10px rgba(0,0,0,.04)}
  .tab{position:absolute;top:18px;width:37px;height:37px;border-radius:50%;border:1.2px solid var(--navy);display:flex;align-items:center;justify-content:center;background:#fff}
  .tab--active{background:var(--navy)}
  .tabbar__indicator{position:absolute;left:137px;top:82px;width:99px;height:3px;border-radius:2px;background:var(--navy)}
</style>
</head>
<body>
<svg width="0" height="0" style="position:absolute">
  <defs>
    <symbol id="i-back" viewBox="0 0 16 16"><circle cx="8" cy="8" r="7.5" fill="currentColor"/><path d="M9.5 4.5L6 8l3.5 3.5" stroke="var(--head-a)" stroke-width="2.2" fill="none"/></symbol>
    <symbol id="i-menu" viewBox="0 0 16 14"><rect y="0" width="16" height="2.6" rx="1" fill="currentColor"/><rect y="5.7" width="16" height="2.6" rx="1" fill="currentColor"/><rect y="11.4" width="16" height="2.6" rx="1" fill="currentColor"/></symbol>
    <symbol id="i-pilot" viewBox="0 0 20 20"><path d="M5 5.5l5-2.5 5 2.5-5 1.2z" fill="currentColor"/><circle cx="10" cy="9" r="3" fill="currentColor"/><path d="M3.5 18c0-4 3-6 6.5-6s6.5 2 6.5 6z" fill="currentColor"/></symbol>
    <symbol id="i-phone" viewBox="0 0 20 20"><path d="M5 3l3 3-1.5 2c1 2 2.5 3.5 4.5 4.5l2-1.5 3 3-2 2C8 15 4 11 3 5z" fill="currentColor"/><path d="M12 5a4 4 0 0 1 3 3M12 2a7 7 0 0 1 6 6" stroke="currentColor" stroke-width="1.4" fill="none"/></symbol>
    <symbol id="i-plane" viewBox="0 0 24 16"><path d="M2 12l4-1 3 1 12-6c2-1 2-3 0-3L16 5 7 2 5 3l6 4-5 2-3-1-2 1z" fill="currentColor"/></symbol>
    <symbol id="i-hand" viewBox="0 0 20 20"><path d="M8 3v8M8 3a1.2 1.2 0 0 1 2.4 0v6l4 1c1.5.5 2 1.5 1.6 3l-1 4H8l-3.5-5c-.6-1 .4-2 1.4-1.3L8 11" stroke="currentColor" stroke-width="1.4" fill="none" stroke-linejoin="round"/></symbol>
    <symbol id="i-gear" viewBox="0 0 20 20"><circle cx="10" cy="10" r="7" stroke="currentColor" stroke-width="1.6" fill="none" stroke-dasharray="3 1.4"/><circle cx="10" cy="10" r="4.2" stroke="currentColor" stroke-width="1.6" fill="none"/><circle cx="10" cy="10" r="1.6" fill="currentColor"/></symbol>
    <symbol id="i-cal" viewBox="0 0 14 14"><rect x="1" y="2.5" width="12" height="10.5" rx="1" stroke="currentColor" stroke-width="1.4" fill="none"/><path d="M1 5.5h12M4 1v3M10 1v3M3.5 8h7M3.5 10.5h7M5.5 5.5v7M8.5 5.5v7" stroke="currentColor" stroke-width="1"/></symbol>
  </defs>
</svg>

<!-- Contact (edit mode) -->
<section class="screen screen--contact">
  <header class="appbar">
    <div class="appbar__title"><svg width="14" height="14" color="#fff"><use href="#i-back"/></svg>Contact</div>
    <div class="appbar__actions"><span class="btn-save">Save</span><svg width="16" height="14" color="#fff"><use href="#i-menu"/></svg></div>
  </header>
  <div class="field" style="left:23px;top:114px;width:326px">Business Name -e</div>
  <div class="field" style="left:23px;top:182px;width:326px">First Name -e</div>
  <div class="field" style="left:23px;top:248px;width:326px">Last Name -e</div>
  <div class="field" style="left:23px;top:329px;width:326px">AddressLabelTag -</div>
  <div class="field" style="left:23px;top:400px;width:326px">AddressLine1-e</div>
  <div class="field" style="left:23px;top:472px;width:326px">AddressLine2-e</div>
  <div class="field" style="left:23px;top:544px;width:326px">AddressCity</div>
  <div class="field" style="left:23px;top:617px;width:153px">AddressState</div>
  <div class="field" style="left:193px;top:617px;width:153px">Zip-e</div>
  <nav class="tabbar">
    <span class="tab tab--active" style="left:24px"><svg width="20" height="20" color="#fff"><use href="#i-phone"/></svg></span>
    <span class="tab" style="left:95px"><svg width="22" height="22" color="var(--navy)"><use href="#i-pilot"/></svg></span>
    <span class="tab" style="left:166px"><svg width="24" height="16" color="var(--navy)"><use href="#i-plane"/></svg></span>
    <span class="tab" style="left:237px"><svg width="20" height="20" color="var(--navy)"><use href="#i-hand"/></svg></span>
    <span class="tab" style="left:308px"><svg width="22" height="22" color="var(--navy)"><use href="#i-gear"/></svg></span>
    <span class="tabbar__indicator"></span>
  </nav>
</section>

<!-- Pilots (list mode) -->
<section class="screen screen--pilots">
  <header class="appbar">
    <div class="appbar__title"><svg width="14" height="14" color="#fff"><use href="#i-back"/></svg>Pilots</div>
    <div class="appbar__actions"><svg width="14" height="14"><path d="M7 0v14M0 7h14" stroke="#fff" stroke-width="3"/></svg><svg width="16" height="14" color="#fff"><use href="#i-menu"/></svg></div>
  </header>
  <div class="card" style="top:105px"><span class="ico badge"><svg width="24" height="24" color="#fff"><use href="#i-pilot"/></svg></span>Adler, Conrad, Blake, 5204817<div class="date"><svg width="15" height="15" color="var(--text)"><use href="#i-cal"/></svg>9/30/24</div></div>
  <div class="card" style="top:197px"><span class="ico badge"><svg width="24" height="24" color="#fff"><use href="#i-pilot"/></svg></span>Bramwell, Roland, 7390264,<div class="date"><svg width="15" height="15" color="var(--text)"><use href="#i-cal"/></svg>2/28/25</div></div>
  <div class="card" style="top:288px"><span class="ico badge"><svg width="24" height="24" color="#fff"><use href="#i-pilot"/></svg></span>Brandvik, Aidan, 8152039<div class="date"><svg width="15" height="15" color="var(--text)"><use href="#i-cal"/></svg>10/30/24, 16</div></div>
  <div class="card" style="top:379px"><span class="ico badge"><svg width="24" height="24" color="#fff"><use href="#i-pilot"/></svg></span>Corsini, Elena, Marisa, 6048213<div class="date"><svg width="15" height="15" color="var(--text)"><use href="#i-cal"/></svg>3/30/25</div></div>
  <div class="card" style="top:470px;line-height:24px"><span class="ico badge"><svg width="24" height="24" color="#fff"><use href="#i-pilot"/></svg></span>Castro Medina, Victor,<br>Anabel,</div>
  <div class="card" style="top:562px"><span class="ico badge"><svg width="24" height="24" color="#fff"><use href="#i-pilot"/></svg></span>Gresham, Colin, 9271546,<div class="date"><svg width="15" height="15" color="var(--text)"><use href="#i-cal"/></svg>2/28/25,</div></div>
  <div class="card" style="top:653px;line-height:37px;padding-top:6px"><span class="ico badge"><svg width="24" height="24" color="#fff"><use href="#i-pilot"/></svg></span>Hollis, Jonah, Everett, 4815720,<div class="date"><svg width="15" height="15" color="var(--text)"><use href="#i-cal"/></svg>3/6/23</div></div>
  <nav class="tabbar">
    <span class="tab" style="left:24px"><svg width="20" height="20" color="var(--navy)"><use href="#i-phone"/></svg></span>
    <span class="tab tab--active" style="left:95px"><svg width="22" height="22" color="#fff"><use href="#i-pilot"/></svg></span>
    <span class="tab" style="left:166px"><svg width="24" height="16" color="var(--navy)"><use href="#i-plane"/></svg></span>
    <span class="tab" style="left:237px"><svg width="20" height="20" color="var(--navy)"><use href="#i-hand"/></svg></span>
    <span class="tab" style="left:308px"><svg width="22" height="22" color="var(--navy)"><use href="#i-gear"/></svg></span>
    <span class="tabbar__indicator"></span>
  </nav>
</section>

<!-- More menu -->
<section class="screen screen--more">
  <header class="appbar">
    <div class="appbar__title"><svg width="14" height="14" color="#fff"><use href="#i-back"/></svg>More</div>
    <div class="appbar__actions"><svg width="16" height="14" color="#fff"><use href="#i-menu"/></svg></div>
  </header>
  <div class="menu-item" style="top:117px"><span class="badge"><svg width="24" height="16" color="#fff"><use href="#i-plane"/></svg></span>Flight</div>
  <div class="menu-item" style="top:176px"><span class="badge"><svg width="20" height="20"><path d="M9 3h7v14H9M3 10h9M9 7l3 3-3 3" stroke="#fff" stroke-width="1.6" fill="none"/></svg></span>Login</div>
  <div class="menu-item" style="top:235px"><span class="badge"><svg width="18" height="18"><circle cx="9" cy="5" r="4" fill="#fff"/><path d="M1 18c0-5 4-7 8-7s8 2 8 7z" fill="#fff"/></svg></span>Account</div>
  <div class="menu-item" style="top:296px"><span class="badge"><svg width="18" height="18"><rect x="1.5" y="3" width="15" height="13.5" rx="1.5" stroke="#fff" stroke-width="1.6" fill="none"/><path d="M1.5 7h15M5 1v4M13 1v4" stroke="#fff" stroke-width="1.6"/></svg></span>Calendar</div>
  <div class="menu-item" style="top:355px"><span class="badge"><svg width="22" height="18"><circle cx="11" cy="5" r="3.2" fill="#fff"/><circle cx="4.5" cy="6" r="2.4" fill="#fff"/><circle cx="17.5" cy="6" r="2.4" fill="#fff"/><path d="M5 17c0-4 3-6 6-6s6 2 6 6zM0 14c0-3 2-4.5 4.5-4.5M22 14c0-3-2-4.5-4.5-4.5" fill="#fff"/></svg></span>Users</div>
  <div class="menu-item" style="top:415px"><span class="badge"><svg width="18" height="18" fill="#fff"><rect x="1" y="1" width="7" height="7" rx="2"/><rect x="10" y="1" width="7" height="7" rx="2"/><rect x="1" y="10" width="7" height="7" rx="2"/><rect x="10" y="10" width="7" height="7" rx="2"/></svg></span>Dashboard</div>
  <div class="menu-item" style="top:474px"><span class="badge"><svg width="20" height="18"><path d="M1 3l6-2 6 2 6-2v14l-6 2-6-2-6 2z" fill="#fff"/><path d="M7 1v15M13 3v15" stroke="var(--navy)" stroke-width="1.4"/></svg></span>Tracking</div>
  <div class="menu-item" style="top:534px"><span class="badge"><svg width="20" height="20"><path d="M3 8l7-3 7 3v9l-7 3-7-3z" fill="#fff"/><path d="M3 8l7 3 7-3M10 11v9" stroke="var(--navy)" stroke-width="1.2" fill="none"/><path d="M12 4l5-3v5z" fill="#fff"/></svg></span>Outreach Event</div>
  <div class="menu-item" style="top:594px"><span class="badge"><svg width="22" height="20" color="#fff"><svg x="0" y="3" width="15" height="15"><use href="#i-gear"/></svg><svg x="12" y="0" width="10" height="10"><use href="#i-gear"/></svg></svg></span>Maintenance Resource</div>
  <div class="menu-item" style="top:653px"><span class="badge"><svg width="20" height="20" color="#fff"><use href="#i-gear"/></svg></span>Setting</div>
  <nav class="tabbar">
    <span class="tab" style="left:24px"><svg width="20" height="20" color="var(--navy)"><use href="#i-phone"/></svg></span>
    <span class="tab" style="left:95px"><svg width="22" height="22" color="var(--navy)"><use href="#i-pilot"/></svg></span>
    <span class="tab" style="left:166px"><svg width="24" height="16" color="var(--navy)"><use href="#i-plane"/></svg></span>
    <span class="tab" style="left:237px"><svg width="20" height="20" color="var(--navy)"><use href="#i-hand"/></svg></span>
    <span class="tab tab--active" style="left:308px"><svg width="22" height="22" color="#fff"><use href="#i-gear"/></svg></span>
    <span class="tabbar__indicator"></span>
  </nav>
</section>
</body>
</html>
```